TeaLantern Flyer

I require an A5 sized flyer to be designed that advertised the new flexible workspace of TeaLantern.
should say it is a "Flexible Workspace with EV Charging"
web address is www.tealantern.co.uk
It should show the 3 different types of membership as priced on the website

```html
<!DOCTYPE html>
<html lang="en">
<head>
<meta charset="utf-8">
<title>TeaLantern Flyer</title>
<link href="https://fonts.googleapis.com/css2?family=Poppins:wght@300;400;500;600;700;800&display=swap" rel="stylesheet">
<style>
:root{
  --orange:#f28c00;
  --ink:#161616;
  --night:#111111;
  --grey:#7b7b7b;
  --blue:#3e6ae0;
  --paper:#ffffff;
}
*{margin:0;padding:0;box-sizing:border-box}
html,body{width:783px;height:1200px;overflow:hidden;background:#f2f2f2}
body{font-family:'Poppins',sans-serif;color:var(--ink)}
svg{display:block}
.flyer{position:relative;width:783px;height:1200px;background:var(--paper);overflow:hidden}

/* hero */
.hero{position:absolute;left:0;top:0;width:783px;height:400px}
.hero-art{position:absolute;left:0;top:0}
.brand{position:absolute;left:44px;top:74px;font-weight:700;font-size:32px;line-height:1;letter-spacing:-0.5px;color:var(--ink);display:flex;align-items:center;gap:8px}
.brand-mark{width:12px;height:12px;background:var(--orange)}
.headline{position:absolute;left:44px;top:148px}
.headline .flex{display:block;font-weight:300;font-size:45px;line-height:44px;letter-spacing:9px;color:var(--ink)}
.headline .work{display:block;font-size:40px;line-height:46px;color:var(--ink)}
.headline .work b{font-weight:700}
.headline .work span{font-weight:400}
.headline .ev{display:block;font-weight:800;font-size:46px;line-height:50px;color:var(--orange)}
.dashes{position:absolute;left:44px;top:300px;display:flex;gap:3px}
.dashes i{display:block;width:9px;height:7px;background:var(--orange)}
.dashes i:nth-child(4){opacity:.7}.dashes i:nth-child(5){opacity:.45}.dashes i:nth-child(6){opacity:.2}
.tagline{position:absolute;left:44px;top:320px;font-size:22px;line-height:1.2;font-weight:400;color:var(--ink)}

/* ev band */
.ev-band{position:absolute;left:0;top:412px;width:783px;height:281px;background:linear-gradient(90deg,#2a2a2a,#1a1a1a 55%,#151515)}
.ev-visual{position:absolute;left:0;top:0;width:450px;height:281px;background:radial-gradient(ellipse at 45% 60%,#d8d8d8 0%,#9a9a9a 22%,#3a3a3a 48%,#222 75%)}
.ev-copy{position:absolute;left:474px;top:26px;width:290px;color:#fff}
.ev-copy h2{font-weight:400;font-size:27px;line-height:1.05}
.ev-copy h2 strong{display:block;font-weight:800;color:var(--orange)}
.ev-copy p{font-size:13px;line-height:1.3;margin-top:14px;font-weight:400}

/* plans */
.plans{position:absolute;left:0;top:706px;width:783px}
.plan{position:absolute;top:30px;width:211px;height:358px;border-radius:18px;padding:0 8px 8px}
.plan.day{left:48px;background:var(--grey);--tone:var(--grey)}
.plan.light{left:285px;background:var(--orange);--tone:var(--orange)}
.plan.all{left:521px;background:var(--blue);--tone:var(--blue)}
.plan-tab{position:absolute;left:50%;top:-30px;width:100px;height:34px;margin-left:-50px;background:var(--tone);border-radius:12px 12px 0 0}
.plan-tab svg{position:absolute;left:38px;top:5px}
.plan h3{height:40px;line-height:40px;text-align:center;color:#fff;font-weight:700;font-size:14.5px}
.plan-body{position:relative;background:#fff;border-radius:14px;height:310px;padding:16px 10px 0 12px}
.perks{list-style:none}
.perks li{position:relative;padding-left:14px;font-size:11.5px;line-height:1.1;margin-bottom:12px;color:#222}
.day .perks li{margin-bottom:17px}
.all .perks li{margin-bottom:7px}
.perks li::before{content:"";position:absolute;left:0;top:2px;width:9px;height:9px;border-radius:50%;background:var(--tone)}
.perks li::after{content:"";position:absolute;left:3px;top:3.5px;width:2px;height:4px;border:solid #fff;border-width:0 1.4px 1.4px 0;transform:rotate(45deg)}
.perks small{display:block;font-size:8.5px;margin-top:2px;color:#444}
.plan-foot{position:absolute;left:0;right:0;bottom:10px;text-align:center}
.monthly{font-weight:700;font-size:13px;margin-bottom:8px}
.price{display:inline-block;background:var(--tone);color:#fff;border-radius:15px;padding:5px 18px;font-size:13px;font-weight:400}
.day .price{background:#3a3a3a}
.price b{font-weight:700}
.vat{font-size:11px;line-height:1.15;margin-top:6px;color:#333}

/* footer */
.footer{position:absolute;left:0;top:1111px;width:783px;height:89px}
.footer-art{position:absolute;left:0;top:0}
.contact{position:absolute;top:32px;display:flex;align-items:center;gap:6px;color:#fff;font-size:11px;font-weight:500;line-height:1.15}
.contact.mail{left:47px}
.contact.pin{left:235px}
.dot{width:17px;height:17px;border-radius:50%;background:var(--orange);display:flex;align-items:center;justify-content:center;flex:none}
.web{position:absolute;left:540px;top:20px;font-size:14px;color:var(--ink)}
.web b{font-weight:700}
</style>
</head>
<body>
<main class="flyer">

  <header class="hero">
    <svg class="hero-art" width="783" height="400" viewBox="0 0 783 400">
      <defs>
        <linearGradient id="lounge" x1="0" y1="0" x2="0" y2="1">
          <stop offset="0" stop-color="#d6d9dc"/>
          <stop offset=".45" stop-color="#8e8c88"/>
          <stop offset=".75" stop-color="#5c4535"/>
          <stop offset="1" stop-color="#6f6c69"/>
        </linearGradient>
      </defs>
      <polygon role="img" aria-label="Photo of the lounge with leather sofas and hot desks" points="515,0 783,0 783,272 742,400 365,400" fill="url(#lounge)"/>
      <polygon points="383,0 512,0 467,128" fill="var(--orange)"/>
      <polygon points="783,285 783,400 748,400" fill="var(--orange)"/>
    </svg>
    <div class="brand"><span class="brand-mark"></span>TeaLantern</div>
    <h1 class="headline">
      <span class="flex">FLEXIBLE</span>
      <span class="work"><b>Workspace</b> <span>with</span></span>
      <span class="ev">EV CHARGING</span>
    </h1>
    <div class="dashes"><i></i><i></i><i></i><i></i><i></i><i></i></div>
    <p class="tagline">Charge your EV, Get some<br>workspace and refuel!</p>
  </header>

  <section class="ev-band">
    <div class="ev-visual" role="img" aria-label="Illustration of a white electric car plugged into a charging post"></div>
    <div class="ev-copy">
      <h2>EV CHARGING AND <strong>WORKSPACE</strong></h2>
      <p>TeaLantern is a unique workspace environment for EV owners looking to recharge their Electric Vehicles, grab a snack and beverage, and catch up with some office work.</p>
      <p>Based just off the A21 in Hollowbrook, we are ideally located for travelling EV owners in and around the Hollowbrook/Weald area.</p>
    </div>
  </section>

  <section class="plans">
    <article class="plan day">
      <div class="plan-tab"><svg width="24" height="24" viewBox="0 0 24 24"><circle cx="12" cy="12" r="9" fill="none" stroke="#fff" stroke-width="2"/></svg></div>
      <h3>DAY MEMBER</h3>
      <div class="plan-body">
        <ul class="perks">
          <li>Use of Hot Desks &amp; Lounge Areas</li>
          <li>Secure Wifi</li>
          <li>Free Tea &amp; Coffee</li>
        </ul>
        <div class="plan-foot">
          <span class="price"><b>£25.00</b> EACH VISIT</span>
          <p class="vat">Price Inclusive of VAT<br>Each Visit</p>
        </div>
      </div>
    </article>

    <article class="plan light">
      <div class="plan-tab"><svg width="24" height="24" viewBox="0 0 24 24"><circle cx="12" cy="12" r="9" fill="none" stroke="#fff" stroke-width="2"/></svg></div>
      <h3>LIGHT MEMBER</h3>
      <div class="plan-body">
        <ul class="perks">
          <li>Use of Hot Desks &amp; Lounge Areas</li>
          <li>Secure Wifi</li>
          <li>Free Tea &amp; Coffee</li>
          <li>Discounted E/V Charge Rates</li>
          <li>Access to Meeting Rooms<small>(£10+vat per person, per hour)</small></li>
        </ul>
        <div class="plan-foot">
          <p class="monthly">£18 a month</p>
          <span class="price"><b>+ £18</b> EACH VISIT</span>
          <p class="vat">Price Inclusive of VAT<br>Each Visit</p>
        </div>
      </div>
    </article>

    <article class="plan all">
      <div class="plan-tab"><svg width="24" height="24" viewBox="0 0 24 24"><circle cx="12" cy="12" r="9" fill="none" stroke="#fff" stroke-width="2"/></svg></div>
      <h3>ALL ACCESS MEMBER</h3>
      <div class="plan-body">
        <ul class="perks">
          <li>Unlimited Number of Visits Each Month</li>
          <li>Dedicated Desk<small>(lockable draws + £60 a month)</small></li>
          <li>Receptionist to Meet &amp; Greet Guests</li>
          <li>Use of Lounge Areas</li>
          <li>Secure Wifi</li>
          <li>Free Tea &amp; Coffee</li>
          <li>Discounted E/V Charge Rates</li>
          <li>Access to Meeting Rooms<small>(£10+vat per person, per hour)</small></li>
        </ul>
        <div class="plan-foot">
          <span class="price"><b>£180.00</b> EACH VISIT</span>
          <p class="vat">Price Inclusive of VAT<br>Each Visit</p>
        </div>
      </div>
    </article>
  </section>

  <footer class="footer">
    <svg class="footer-art" width="783" height="89" viewBox="0 0 783 89">
      <polygon points="0,0 474,0 542,83 783,83 783,89 0,89" fill="var(--night)"/>
      <polygon points="492,8 500,8 560,82 552,82" fill="var(--orange)"/>
    </svg>
    <div class="contact mail">
      <span class="dot"><svg width="9" height="7" viewBox="0 0 9 7"><rect x=".5" y=".5" width="8" height="6" fill="none" stroke="#fff"/><path d="M.5 .5 4.5 4 8.5 .5" fill="none" stroke="#fff"/></svg></span>
      <span>info@tealantern.co.uk</span>
    </div>
    <div class="contact pin">
      <span class="dot"><svg width="8" height="10" viewBox="0 0 8 10"><path d="M4 10C1.5 6.5 0 5 0 3.5a4 4 0 0 1 8 0C8 5 6.5 6.5 4 10z" fill="#fff"/><circle cx="4" cy="3.6" r="1.4" fill="var(--orange)"/></svg></span>
      <span>Lantern Row, Hollowbrook HB4<br>2TL United Kingdom</span>
    </div>
    <p class="web">www.<b>tealantern</b>.co.uk</p>
  </footer>

</main>
</body>
</html>
```